Torvane Halbridge

Looking for modern business cards.
Clean contemporary design.
Similar to this.
https://www.plumvexa-search.example/imgres?imgurl=https%3A%2F%2Fimg.quorlint-cdn.example%2Fsleek_dark_metal_card_design_540.jpg&imgrefurl=https%3A%2F%2Fwww.quorlint-prints.example%2Fsleek_dark_metal_card_design-918273645501928374&q=modern%20business%20cards

But I'd like the blue to look metallic.

Business

```html
<!DOCTYPE html>
<html lang="en">
<head>
<meta charset="utf-8">
<title>Torvane Halbridge – Business Card</title>
<link href="https://fonts.googleapis.com/css2?family=Roboto:wght@700&family=Lato:wght@400&display=swap" rel="stylesheet">
<style>
  :root {
    --page-bg: #e9ecee;
    --card-white: #ffffff;
    --steel-dark: #1b4a61;
    --steel-mid: #2a6584;
    --steel-light: #4f89a6;
    --swoosh-pale: #c9e3ee;
    --brand-blue: #2a5d78;
    --accent-red: #e8381f;
    --text-light: #ffffff;
  }
  html, body {
    margin: 0;
    width: 1200px;
    height: 900px;
    overflow: hidden;
    background: var(--page-bg);
  }
  .business-card {
    position: absolute;
    left: 160px;
    top: 178px;
    width: 880px;
    height: 544px;
    background: var(--card-white);
    box-shadow: 0 10px 30px rgba(20, 50, 70, 0.18);
    overflow: hidden;
  }
  .card-shapes {
    position: absolute;
    inset: 0;
    width: 100%;
    height: 100%;
  }
  .brand {
    position: absolute;
    left: 48px;
    top: 322px;
  }
  .brand-name {
    display: flex;
    align-items: center;
    gap: 12px;
    font-family: "Lato", sans-serif;
    font-weight: 400;
    font-size: 42px;
    line-height: 1;
    color: var(--brand-blue);
    letter-spacing: -0.5px;
  }
  .brand-dot {
    width: 14px;
    height: 14px;
    border-radius: 50%;
    background: var(--accent-red);
  }
  .brand-tagline {
    margin-top: 6px;
    font-family: "Lato", sans-serif;
    font-size: 10px;
    color: var(--steel-light);
  }
  .person {
    position: absolute;
    right: 34px;
    top: 102px;
    text-align: right;
    color: var(--text-light);
  }
  .person-name {
    font-family: "Roboto", sans-serif;
    font-weight: 700;
    font-size: 30px;
    letter-spacing: 0.3px;
    line-height: 1.1;
  }
  .person-title {
    font-family: "Lato", sans-serif;
    font-size: 23px;
    margin-top: 4px;
  }
  .contacts {
    position: absolute;
    right: 34px;
    top: 378px;
    margin: 0;
    padding: 0;
    list-style: none;
    text-align: right;
    font-family: "Lato", sans-serif;
    font-size: 23px;
    color: var(--text-light);
  }
  .contact-item {
    display: flex;
    justify-content: flex-end;
    align-items: center;
    gap: 8px;
    height: 34px;
  }
  .contact-icon {
    width: 18px;
    height: 18px;
    fill: var(--text-light);
  }
</style>
</head>
<body>
  <main class="business-card">
    <svg class="card-shapes" viewBox="0 0 650 402" preserveAspectRatio="none" aria-hidden="true">
      <defs>
        <linearGradient id="steel-gradient" x1="0" y1="0" x2="1" y2="1">
          <stop offset="0" stop-color="#3b7695"/>
          <stop offset="0.3" stop-color="#1e5069"/>
          <stop offset="0.55" stop-color="#4a86a4"/>
          <stop offset="0.75" stop-color="#215870"/>
          <stop offset="1" stop-color="#173f53"/>
        </linearGradient>
      </defs>
      <path class="swoosh-pale" fill="var(--swoosh-pale)"
            d="M30,92 C90,28 180,2 255,0 L275,0 C185,10 100,42 30,92 Z"/>
      <path class="steel-panel" fill="url(#steel-gradient)"
            d="M32,97 C100,35 190,5 250,0 L650,0 L650,402 L362,402
               C405,320 410,190 340,115 C270,45 140,45 32,97 Z"/>
    </svg>

    <div class="brand">
      <div class="brand-name"><span>Torvane Halbridge</span><span class="brand-dot"></span></div>
      <div class="brand-tagline">Steady Leadership for Companies That Grow</div>
    </div>

    <div class="person">
      <div class="person-name">CORWIN ASHDALE</div>
      <div class="person-title">Managing Director</div>
    </div>

    <ul class="contacts">
      <li class="contact-item">444 555 2917
        <svg class="contact-icon" viewBox="0 0 24 24"><path d="M3 8c0-3 4-4 9-4s9 1 9 4v2h-5V8H8v2H3z M6 12h12l2 8H4z M12 14a2.5 2.5 0 1 0 0.01 0z"/></svg>
      </li>
      <li class="contact-item">info@halbridge.example
        <svg class="contact-icon" viewBox="0 0 24 24"><path d="M3 6h18v12H3z M4.5 7.5 12 13l7.5-5.5" stroke="#1e5069" stroke-width="1.5"/></svg>
      </li>
      <li class="contact-item">www.halbridge.example
        <svg class="contact-icon" viewBox="0 0 24 24"><circle cx="12" cy="12" r="9"/><path d="M3 12h18 M12 3c-3 3-3 15 0 18 M12 3c3 3 3 15 0 18" stroke="#1e5069" stroke-width="1.4" fill="none"/></svg>
      </li>
    </ul>
  </main>
</body>
</html>
```